Business cards for KORU Real Estate Holdings LLC

We need a cool, original business card design for a company based in the Washington DC metropolitan area. We are a new energetic and passionate Real Estate Investing Company that invests in all types of real estate; commercial, residential, industrial etc.

Our company color is Red since it reflects action, energy and speed; it is assertive confident, energizing, exciting, powerful, passionate and determined. So we would like business card communicate those qualities to the audience.

Our audiences are investors that want to invest with us, real estate sellers, buyers, and tenants who lease from us.

Our logo is attached

```html
<!DOCTYPE html>
<html lang="en">
<head>
<meta charset="utf-8">
<title>KORU Real Estate Holdings LLC — Business Card</title>
<link rel="stylesheet" href="https://fonts.googleapis.com/css2?family=Open+Sans:wght@400;600;700;800&display=swap">
<style>
  :root {
    --page-bg: #d9d6d0;
    --card-bg: #ecebe8;
    --card-edge: #f7f6f4;
    --band-dark: #55565a;
    --band-light: #8d8e92;
    --brand-red: #d8262c;
    --ink: #3a3a3c;
    --ink-soft: #4c4c4e;
    --accent-gold: #e6ad0b;
  }
  * { margin: 0; padding: 0; box-sizing: border-box; }
  html, body {
    width: 1200px;
    height: 801px;
    overflow: hidden;
    background: var(--page-bg);
    font-family: "Open Sans", Arial, sans-serif;
  }
  .business-card {
    position: absolute;
    left: 163px;
    top: 141px;
    width: 874px;
    height: 501px;
    border-radius: 32px;
    background: var(--card-bg);
    border: 2px solid var(--card-edge);
    box-shadow: 0 10px 30px rgba(0,0,0,0.12);
    overflow: hidden;
  }
  .side-band {
    position: absolute;
    left: 45px;
    top: 0;
    width: 86px;
    height: 100%;
    background: var(--band-dark);
  }
  .side-band-line {
    position: absolute;
    left: 58px;
    top: 0;
    width: 5px;
    height: 100%;
    background: var(--band-light);
  }
  .brand {
    position: absolute;
    left: 214px;
    top: 116px;
    display: flex;
    align-items: center;
    gap: 26px;
  }
  .brand-mark {
    width: 74px;
    height: 74px;
    background: var(--brand-red);
  }
  .brand-name {
    font-size: 88px;
    font-weight: 800;
    line-height: 1;
    letter-spacing: 2px;
    color: var(--ink);
  }
  .address {
    position: absolute;
    left: 221px;
    top: 304px;
    font-size: 21px;
    line-height: 30px;
    color: var(--ink);
  }
  .contact-list {
    position: absolute;
    left: 224px;
    top: 366px;
    list-style: none;
    font-size: 17px;
    line-height: 27.5px;
    color: var(--ink-soft);
  }
  .contact-list li {
    display: flex;
    align-items: center;
    gap: 14px;
  }
  .contact-icon {
    width: 17px;
    height: 17px;
    flex: none;
  }
  .person {
    position: absolute;
    right: 56px;
    top: 410px;
    text-align: right;
  }
  .person-name {
    font-size: 30px;
    line-height: 36px;
    font-weight: 400;
    color: var(--ink);
  }
  .person-name .first-name {
    color: var(--accent-gold);
  }
  .person-title {
    font-size: 18px;
    line-height: 26px;
    color: var(--ink-soft);
  }
</style>
</head>
<body>
  <div class="business-card">
    <div class="side-band"></div>
    <div class="side-band-line"></div>

    <div class="brand">
      <div class="brand-mark"></div>
      <div class="brand-name">KORU</div>
    </div>

    <div class="address">
      <p>Suite 410, 88 Elm Row</p>
      <p>Arlington, VA 22201</p>
    </div>

    <ul class="contact-list">
      <li>
        <svg class="contact-icon" viewBox="0 0 24 24" aria-hidden="true"><path fill="#e6ad0b" d="M6.6 10.8a15.1 15.1 0 0 0 6.6 6.6l2.2-2.2a1 1 0 0 1 1-.25 11.4 11.4 0 0 0 3.6.57 1 1 0 0 1 1 1V20a1 1 0 0 1-1 1A17 17 0 0 1 3 4a1 1 0 0 1 1-1h3.5a1 1 0 0 1 1 1c0 1.25.2 2.45.57 3.57a1 1 0 0 1-.25 1z"/></svg>
        <span>202-555-0147</span>
      </li>
      <li>
        <svg class="contact-icon" viewBox="0 0 24 24" aria-hidden="true"><path fill="#e6ad0b" d="M6.6 10.8a15.1 15.1 0 0 0 6.6 6.6l2.2-2.2a1 1 0 0 1 1-.25 11.4 11.4 0 0 0 3.6.57 1 1 0 0 1 1 1V20a1 1 0 0 1-1 1A17 17 0 0 1 3 4a1 1 0 0 1 1-1h3.5a1 1 0 0 1 1 1c0 1.25.2 2.45.57 3.57a1 1 0 0 1-.25 1z"/></svg>
        <span>202-555-0183</span>
      </li>
      <li>
        <svg class="contact-icon" viewBox="0 0 24 24" aria-hidden="true"><path fill="#e6ad0b" d="M6.6 10.8a15.1 15.1 0 0 0 6.6 6.6l2.2-2.2a1 1 0 0 1 1-.25 11.4 11.4 0 0 0 3.6.57 1 1 0 0 1 1 1V20a1 1 0 0 1-1 1A17 17 0 0 1 3 4a1 1 0 0 1 1-1h3.5a1 1 0 0 1 1 1c0 1.25.2 2.45.57 3.57a1 1 0 0 1-.25 1z"/></svg>
        <span>703-555-0129</span>
      </li>
      <li>
        <svg class="contact-icon" viewBox="0 0 24 24" aria-hidden="true"><rect x="2" y="5" width="20" height="14" rx="2" fill="#e6ad0b"/><path d="M3 6.5l9 6.5 9-6.5" fill="none" stroke="#ecebe8" stroke-width="1.8"/></svg>
        <span>dan@koruhold.com</span>
      </li>
    </ul>

    <div class="person">
      <p class="person-name"><span class="first-name">Daniel</span> Reyes</p>
      <p class="person-title">Owner / C.E.O.</p>
    </div>
  </div>
</body>
</html>
```